Pup Snack Den - New Website Design

Create a professional Storvana website for a the hottest trend; a Pup Snack Den subscription box business. Storvana.com is an easy to use website builder.
Please see frellonbox.com; gummotrove.com and wagcrate.com for the concept I am after. The business has not been launched yet, I am currently in the pre-launch stage using a specialized landing page website, and so the time scale for developing my professional looking Storvana website is up to 1-2 weeks.
The webpage should have a fun feel and should match the style of the company logo at gummotrove.com. The pages to include are 'Home', 'About us' and 'Get Started'
Thank you and good luck!

```html
<!DOCTYPE html>
<html lang="en">
<head>
<meta charset="utf-8">
<title>Pup Snack Den</title>
<link href="https://fonts.googleapis.com/css2?family=Raleway:wght@500;700;800&family=Open+Sans:wght@400;600;700&display=swap" rel="stylesheet">
<style>
:root{
  --page:#f3f3f4;
  --white:#ffffff;
  --ink:#1c1c1c;
  --body:#555a60;
  --blue:#1f5ea8;
  --navy:#1b3a7e;
  --orange:#f3700f;
  --green:#2aa01f;
  --dark:#2b2b2d;
  --line:#dcdcdc;
}
*{margin:0;padding:0;box-sizing:border-box}
html,body{width:1200px;height:4478px;overflow:hidden}
body{background:var(--page);font-family:"Open Sans",Arial,sans-serif;color:var(--body);position:relative}
.ph{position:absolute}
h2.section-title{position:absolute;left:0;width:1200px;text-align:center;font-family:"Raleway",Arial,sans-serif;font-weight:800;font-size:26px;color:var(--ink);letter-spacing:1px}

/* header */
.site-header{position:absolute;top:0;left:0;width:1200px;height:84px;background:var(--white)}
.logo{position:absolute;left:75px;top:26px;font-family:"Raleway",Arial,sans-serif;font-weight:800;font-size:27px;color:var(--ink)}
.main-nav{position:absolute;left:313px;top:34px;display:flex;gap:38px;list-style:none;font-family:"Raleway",Arial,sans-serif;font-weight:700;font-size:12.5px;color:var(--ink)}
.btn{display:flex;align-items:center;justify-content:center;font-family:"Raleway",Arial,sans-serif;font-weight:700;font-size:13px;color:#fff;letter-spacing:.5px}
.btn-login{position:absolute;left:907px;top:24px;width:102px;height:33px;background:var(--orange)}
.btn-start{position:absolute;left:1024px;top:24px;width:101px;height:33px;background:var(--green)}

/* hero */
.hero-backdrop{left:612px;top:75px;width:588px;height:603px;background:linear-gradient(135deg,#2a4f9a,#173576 60%,#10285c)}
.hero-card{position:absolute;left:75px;top:158px;width:898px;height:439px;background:linear-gradient(90deg,#f4f5f4,#e9eae8)}
.hero-photo{left:432px;top:0;width:466px;height:439px;background:radial-gradient(ellipse at 45% 55%,#5b4638 0%,#8d7d70 30%,#e6e4df 65%,#eeeeec 100%)}
.hero-title{position:absolute;left:38px;top:122px;font-family:"Raleway",Arial,sans-serif;font-weight:700;font-size:38px;line-height:47px;color:var(--blue)}
.btn-sub{position:absolute;left:38px;top:248px;width:156px;height:40px;background:var(--green)}
.btn-gift{position:absolute;left:212px;top:248px;width:156px;height:40px;border:2px solid #777;color:var(--ink)}
.hero-arrow{position:absolute;top:362px}

/* welcome */
.welcome-photo{left:75px;top:749px;width:421px;height:391px;background:linear-gradient(135deg,#23448a,#16316c)}
.welcome-title{position:absolute;left:110px;top:890px;font-family:"Raleway",Arial,sans-serif;font-weight:800;font-size:42px;line-height:52px;color:#fff}
.welcome-text{position:absolute;left:496px;top:749px;width:629px;height:391px;background:var(--white);padding:86px 40px 0 30px;font-size:14px;line-height:24px}
.welcome-text p+p{margin-top:22px}

/* feature cards */
.feature{position:absolute;top:1173px;width:331px;height:397px;background:var(--white)}
.feature .ph{left:0;top:0;width:331px;height:293px}
.feature-label{position:absolute;left:0;top:293px;width:331px;height:104px;background:var(--orange);display:flex;align-items:center;justify-content:center;font-family:"Raleway",Arial,sans-serif;font-weight:800;font-size:22px;color:#fff;letter-spacing:.5px}

/* testimonials */
.testimonial{position:absolute;top:1785px;width:331px;height:194px;background:var(--white);text-align:center;padding:52px 30px 0}
.avatar{position:absolute;top:1719px;width:102px;height:102px;border-radius:50%;border:4px solid #fff}
.testimonial h3{font-family:"Raleway",Arial,sans-serif;font-weight:700;font-size:13px;color:var(--blue);margin-bottom:8px}
.testimonial p{font-size:13px;line-height:20px}

/* banner */
.banner{left:0;top:2051px;width:1200px;height:340px;background:linear-gradient(90deg,#2d2d30,#4a4746 50%,#2f2f31)}
.banner-text{position:absolute;left:0;top:2175px;width:1200px;text-align:center;font-family:"Raleway",Arial,sans-serif;font-weight:800;font-size:31px;line-height:44px;color:#fff;letter-spacing:1px}

/* memberships */
.plan{position:absolute;top:2543px;width:331px;height:397px;background:var(--white);text-align:center}
.plan .ph{left:15px;top:10px;width:301px;height:210px}
.plan h3{position:absolute;left:0;top:243px;width:100%;font-family:"Raleway",Arial,sans-serif;font-weight:800;font-size:18px;color:var(--blue)}
.price{position:absolute;left:0;top:275px;width:100%;font-family:"Raleway",Arial,sans-serif;font-weight:800;font-size:25px;color:var(--orange)}
.price small{font-size:11px}
.btn-plan{position:absolute;left:75px;top:317px;width:181px;height:42px;background:#1a1a1a}

/* blog */
.blog{position:absolute;left:75px;top:3096px;width:1050px;height:394px;background:var(--white)}
.blog .ph{left:0;top:0;width:525px;height:394px;background:linear-gradient(135deg,#d9d4cc,#b9a792 45%,#e7e3de)}
.blog-body{position:absolute;left:561px;top:88px;width:455px}
.blog-date{font-family:"Raleway",Arial,sans-serif;font-weight:800;font-size:13px;color:var(--blue)}
.blog-body h3{font-family:"Raleway",Arial,sans-serif;font-weight:800;font-size:17px;color:var(--ink);margin:10px 0 12px}
.blog-body p{font-size:14px;line-height:24px}
.more{margin-top:22px;font-family:"Raleway",Arial,sans-serif;font-weight:800;font-size:12px;color:var(--ink)}

/* photo feed */
.feed{position:absolute;top:3618px;height:248px}
.feed-card{position:absolute;left:315px;top:3657px;width:282px;height:170px;background:var(--white);padding:16px 22px;font-size:12.5px;line-height:19px}
.likes{font-weight:700;color:var(--ink);display:flex;align-items:center;gap:8px;margin-bottom:8px}
.feed-date{margin-top:12px;font-family:"Raleway",Arial,sans-serif;font-weight:800;font-size:12px;color:var(--orange)}

/* newsletter */
.newsletter{left:0;top:3928px;width:1200px;height:194px;background:linear-gradient(90deg,#313131,#3f3f3f 60%,#343434)}
.news-title{position:absolute;left:135px;top:4015px;font-family:"Raleway",Arial,sans-serif;font-weight:800;font-size:20px;color:#fff;letter-spacing:.5px}
.news-input{position:absolute;left:528px;top:4000px;width:475px;height:54px;background:#fff;padding:0 16px;display:flex;align-items:center;font-size:13px;color:#555}
.news-send{position:absolute;left:1003px;top:4000px;width:63px;height:54px;background:var(--orange);display:flex;align-items:center;justify-content:center}

/* footer */
.footer-col{position:absolute;top:4164px;width:240px;font-size:12.5px;line-height:20px}
.footer-col h4{font-family:"Raleway",Arial,sans-serif;font-weight:800;font-size:14px;color:var(--blue);margin-bottom:10px}
.footer-col ul{list-style:none;line-height:25px}
.contact-row{display:flex;align-items:center;gap:14px;margin-bottom:10px}
.feed-note a{color:var(--blue);text-decoration:none}
.posted{margin-top:10px;font-family:"Raleway",Arial,sans-serif;font-weight:700;font-size:10.5px;color:var(--ink)}
.footer-bottom{position:absolute;left:75px;top:4405px;width:1050px;border-top:1px solid var(--line);padding-top:25px;font-size:11px}
</style>
</head>
<body>

<header class="site-header">
  <div class="logo">Pup Snack Den</div>
  <ul class="main-nav">
    <li>HOME</li><li>WHAT IS IT</li><li>WHAT'S INSIDE</li><li>MEMBERSHIP</li><li>BLOG</li><li>CONTACT</li>
  </ul>
  <div class="btn btn-login">LOG IN</div>
  <div class="btn btn-start">GET STARTED</div>
</header>

<section class="hero">
  <div class="ph hero-backdrop" role="img" aria-label="Photo of a dog in deep blue tones"></div>
  <div class="hero-card">
    <div class="ph hero-photo" role="img" aria-label="Photo of a small puppy sitting beside a red gift box"></div>
    <h1 class="hero-title">Aliquam ullamcorper<br>tempor felis.</h1>
    <div class="btn btn-sub">SUBSCRIBE</div>
    <div class="btn btn-gift">GIVE A GIFT</div>
    <svg class="hero-arrow" style="left:837px" width="20" height="32" viewBox="0 0 20 32"><path d="M16 3 L4 16 L16 29" fill="none" stroke="#fff" stroke-width="3"/></svg>
    <svg class="hero-arrow" style="left:942px" width="20" height="32" viewBox="0 0 20 32"><path d="M4 3 L16 16 L4 29" fill="none" stroke="#fff" stroke-width="3"/></svg>
  </div>
</section>

<section class="welcome">
  <div class="ph welcome-photo" role="img" aria-label="Photo of a white puppy with a blue tint"></div>
  <h2 class="welcome-title">Welcome to<br>Pup Snack Den</h2>
  <div class="welcome-text">
    <p>Aliquam molestie, mi et imperdiet euismod, dui purus auctor tellus, et interdum lacus lectus et ante. Sed accumsan sollicitudin sapien, sit amet adipiscing turpis gravida ac. In congue, neque ac lobortis volutpat, libero mauris varius mi, vitae suscipit ipsum ligula vitae risus.</p>
    <p>Duis aliquam nibh a dui iaculis viverra sit a velit. Vivamus egestas risus in magna varius commodo. Sed semper viverra egestas. Etiam pretium porttitor lectus, vel ornare neque porta volutpat. Aenean a nibh eget turpis vehicula tempus ac sed massa. Vestibulum dolor nulla, ultrices ac tincidunt sed, laoreet non est.</p>
  </div>
</section>

<section class="features">
  <div class="feature" style="left:75px"><div class="ph" role="img" aria-label="Photo of a puppy sniffing small gift boxes" style="background:linear-gradient(135deg,#fafafa,#e8d8c6 55%,#f5f5f5)"></div><div class="feature-label">WHAT IS IT</div></div>
  <div class="feature" style="left:436px"><div class="ph" role="img" aria-label="Photo of a puppy peeking out of an open white gift box" style="background:linear-gradient(135deg,#fbfbfb,#eee7e6 55%,#f7f7f7)"></div><div class="feature-label">WHAT'S INSIDE</div></div>
  <div class="feature" style="left:794px"><div class="ph" role="img" aria-label="Photo of a white puppy in a golden gift box" style="background:linear-gradient(135deg,#f6f3ea,#d7b44f 60%,#f2e7c8)"></div><div class="feature-label">INSPIRED BY DOGS</div></div>
</section>

<h2 class="section-title" style="top:1648px">TESTIMONIALS</h2>
<section class="testimonials">
  <div class="testimonial" style="left:75px"><h3>NAME HEADING</h3><p>Aliquam molestie, mi et imperdiet euismod, dui purus auctor tellus, et interdum lacus lectus et ante aliquam nibh a dui iaculis</p></div>
  <div class="testimonial" style="left:436px"><h3>NAME HEADING</h3><p>Aliquam molestie, mi et imperdiet euismod, dui purus auctor tellus, et interdum lacus lectus et ante aliquam nibh a dui iaculis</p></div>
  <div class="testimonial" style="left:794px"><h3>NAME HEADING</h3><p>Aliquam molestie, mi et imperdiet euismod, dui purus auctor tellus, et interdum lacus lectus et ante aliquam nibh a dui iaculis</p></div>
  <div class="avatar" role="img" aria-label="Customer portrait" style="left:189px;background:linear-gradient(#c8b5a3,#8f7a6a)"></div>
  <div class="avatar" role="img" aria-label="Customer portrait" style="left:550px;background:linear-gradient(#e2cfa4,#b08a5c)"></div>
  <div class="avatar" role="img" aria-label="Customer portrait" style="left:908px;background:linear-gradient(#a9a9ab,#5c5d61)"></div>
</section>

<section>
  <div class="ph banner" role="img" aria-label="Photo of a puppy wearing a pink party hat"></div>
  <div class="banner-text">ALIQUAM MOLESTIE, MI ET IMPERDIET EUISMOD,<br>DUI PURUS AUCTOR TELLUS</div>
</section>

<h2 class="section-title" style="top:2460px">MEMBERSHIPS</h2>
<section class="plans">
  <div class="plan" style="left:75px"><div class="ph" role="img" aria-label="Photo of a fluffy puppy beside a red gift box" style="background:linear-gradient(135deg,#fff,#e7b98a 45%,#d94a5a 75%,#fff)"></div><h3>NAM FERMENTUM</h3><div class="price">$12.00<small>/PM</small></div><div class="btn btn-plan">SUBSCRIBE</div></div>
  <div class="plan" style="left:436px"><div class="ph" role="img" aria-label="Photo of a puppy lying by a stack of gift boxes" style="background:linear-gradient(135deg,#fff,#c98a52 45%,#e5c18f 75%,#fff)"></div><h3>NAM FERMENTUM</h3><div class="price">$12.00<small>/PM</small></div><div class="btn btn-plan">SUBSCRIBE</div></div>
  <div class="plan" style="left:794px"><div class="ph" role="img" aria-label="Photo of a puppy with red presents on a white table" style="background:linear-gradient(135deg,#fff,#5a3a2c 40%,#d63c3c 70%,#f0f0f0)"></div><h3>NAM FERMENTUM</h3><div class="price">$12.00<small>/PM</small></div><div class="btn btn-plan">SUBSCRIBE</div></div>
</section>

<h2 class="section-title" style="top:3024px">OUR LATEST BLOG</h2>
<article class="blog">
  <div class="ph" role="img" aria-label="Photo of a puppy asleep beside a teddy bear"></div>
  <div class="blog-body">
    <div class="blog-date">JUL 07, 2017</div>
    <h3>ALIQUAM MOLESTIE MI ET IMPERDIET</h3>
    <p>Sed accumsan sollicitudin sapien, sit amet adipiscing turpis gravida ac. In congue, neque ac lobortis volutpat, libero mauris varius mi, vitae suscipit ipsum ligula vitae risus in magna varius commodo. Sed semper viverra egestas. Etiam pretium porttitor lectus, vel ornare neque porta volutpat.</p>
    <div class="more">CONTINUE READING</div>
  </div>
</article>

<h2 class="section-title" style="top:3549px">FOLLOW US ON SNAPSHELF</h2>
<section>
  <div class="feed ph" role="img" aria-label="Photo of a puppy with gifts" style="left:0;width:156px;background:linear-gradient(135deg,#e7dfd4,#b58a5e)"></div>
  <div class="feed ph" role="img" aria-label="Photo of a puppy in a party hat" style="left:156px;width:157px;background:linear-gradient(135deg,#d9d3d3,#8b7063)"></div>
  <div class="feed-card">
    <div class="likes"><svg width="14" height="13" viewBox="0 0 14 13"><path d="M7 12 L1.5 6.5 A3 3 0 0 1 7 2.5 A3 3 0 0 1 12.5 6.5 Z" fill="#222"/></svg>254</div>
    <p>Lorem ipsum dolor sit amet, consect- etuer adipiscing elit. Sed diam nonummy nibh euismod tincidunt ut laoreet dolore magna aliquam erat volutpat.</p>
    <div class="feed-date">JULY 07, 2017</div>
  </div>
  <div class="feed ph" role="img" aria-label="Photo of a puppy among brown treats" style="left:600px;width:284px;background:linear-gradient(135deg,#7a4a2e,#c08a5b 50%,#5e3a22)"></div>
  <div class="feed ph" role="img" aria-label="Photo of a small puppy close up" style="left:884px;width:155px;background:linear-gradient(135deg,#d8d2cc,#9d8572)"></div>
  <div class="feed ph" role="img" aria-label="Photo of a dog in blue tones" style="left:1039px;width:161px;background:linear-gradient(135deg,#2a58a8,#163a7e)"></div>
</section>

<section>
  <div class="ph newsletter" role="img" aria-label="Dark photo backdrop"></div>
  <div class="news-title">SUBSCRIBE TO OUR NEWSLETTE</div>
  <div class="news-input">Enter Email Address</div>
  <div class="news-send"><svg width="22" height="22" viewBox="0 0 22 22"><path d="M2 10 L20 2 L13 20 L10 12 Z" fill="#fff"/></svg></div>
</section>

<footer>
  <div class="footer-col" style="left:75px;width:210px">
    <h4>ABOUT US</h4>
    <p>Vestibulum vel metus sit amet turpis bibendum tincidunt vel sit amet quam. Pellentesque habitant morbi tristique senectus et netus et malesuada fames ac.</p>
  </div>
  <div class="footer-col" style="left:367px">
    <h4>SITE MAP</h4>
    <ul><li>Home</li><li>What is it</li><li>What's Inside</li><li>Membership</li><li>Blog</li><li>Contact</li></ul>
  </div>
  <div class="footer-col" style="left:594px">
    <h4>CONTACT US</h4>
    <div class="contact-row"><svg width="14" height="11" viewBox="0 0 14 11"><rect x=".5" y=".5" width="13" height="10" fill="none" stroke="#555"/><path d="M.5 .5 L7 6 L13.5 .5" fill="none" stroke="#555"/></svg>hello@pupsnackden.com</div>
    <div class="contact-row"><svg width="14" height="14" viewBox="0 0 14 14"><path d="M3 1 L5.5 4 L4 6 Q6 9 8 10 L10 8.5 L13 11 L11 13 Q4 12 1 3 Z" fill="#555"/></svg>1-800-555-0142</div>
  </div>
  <div class="footer-col feed-note" style="left:884px;width:200px">
    <h4>CHIRPLINE FEEDS</h4>
    <p>Vestibulum vel metus sit amet turpis <a>bibendum bibendum</a> vel sit amet quam.</p>
    <div class="posted">POSTED 14 HOURS AGO</div>
  </div>
  <div class="footer-bottom">Copyright © 2017 Pup Snack Den. All Right Reserved</div>
</footer>

</body>
</html>
```